Kestrel Baseball & Softball Camp 2017

Design a flyer that will promote our 2017 summer camp for boys and girls softball.

Weeks of
July 10th - 14th
July 17th - 21st.

Players ages 5 - 11.
Full day = 9:30am - 2:30pm half day = 9:30am - 11:30am.
$295 / full day : $195/ half day

Hosted by "Kestrel Baseball" affiliated with the Harbor Comets Travel Baseball & Softball Club and the Maple Ridge Youth League,

Camp Location MRYL, Route 9C Birch Hollow.

PHone 555-240-7813, email info@kestrelball.example

The color should be "Red white and blue color scheme" with dates and location standing out. Kestrel Logo should be prominent MRYL and Comets smaller and secondary.

Feel free to use stock photo's if available. visit www.harborcomets.example for more pictures and there are links for the 2017 summer camp there with possibly some more information.

Target Market(s)

to catch the eye of parents of players ages 5 - 11 already at little league or shopping in local stores

Colors
ec1f27
0355a3
ffffff

Requirements
Must have
• red white and blue design,
• Kestrel logo and summer camp prominent so it catches the eye and explains what it is right away.
• the comets and maple ridge logo's a the bottom showing the affiliation.
Nice to have
• stock photo's or something showing players having a great time or a beautiful ballpark
Should not have
• to much clutter or hard to figure out what it's for

```html
<!DOCTYPE html>
<html lang="en">
<head>
<meta charset="utf-8">
<title>Kestrel Softball Summer Camp 2017</title>
<link href="https://fonts.googleapis.com/css2?family=Oswald:wght@400;500;600;700&family=Kaushan+Script&display=swap" rel="stylesheet">
<style>
  :root {
    --red: #ec1f27;
    --blue: #0355a3;
    --navy: #1f3a6e;
    --white: #ffffff;
    --ink: #1b1b1b;
    --grass-light: #8c9a5a;
    --grass-dark: #4f5a2e;
  }
  html, body {
    margin: 0;
    padding: 0;
    width: 818px;
    height: 1200px;
    overflow: hidden;
    background: var(--white);
  }
  .flyer {
    position: relative;
    width: 818px;
    height: 1200px;
    overflow: hidden;
    font-family: "Oswald", sans-serif;
    color: var(--white);
    white-space: nowrap;
  }
  .flyer__backdrop, .flyer__titles {
    position: absolute;
    left: 0;
    top: 0;
  }
  .brand-badge {
    position: absolute;
    left: 100px;
    top: 282px;
    width: 184px;
    height: 184px;
    display: flex;
    align-items: center;
    justify-content: center;
    font-weight: 700;
    font-size: 44px;
    color: var(--red);
    letter-spacing: 1px;
  }
  .title-script {
    position: absolute;
    left: 492px;
    top: 458px;
    font-family: "Kaushan Script", cursive;
    font-size: 56px;
    color: var(--red);
    line-height: 1;
  }
  .title-sub {
    position: absolute;
    left: 480px;
    top: 650px;
    font-family: "Kaushan Script", cursive;
    font-size: 26px;
    color: var(--navy);
    line-height: 1.2;
  }
  .affiliate-badge {
    position: absolute;
    left: 248px;
    top: 734px;
    width: 58px;
    height: 58px;
    background: #e8efe0;
    border: 2px solid var(--blue);
    border-radius: 4px;
  }
  .players {
    position: absolute;
    left: 512px;
    top: 846px;
    display: flex;
    align-items: flex-start;
    gap: 10px;
  }
  .players__label {
    font-size: 25px;
    font-weight: 600;
    line-height: 1.1;
    text-transform: uppercase;
  }
  .players__ages {
    position: absolute;
    left: 660px;
    top: 823px;
    width: 102px;
    height: 102px;
    border-radius: 50%;
    background: var(--navy);
    display: flex;
    align-items: center;
    justify-content: center;
    font-size: 32px;
    font-weight: 600;
  }
  .info-col {
    position: absolute;
    top: 936px;
    text-transform: uppercase;
    font-weight: 500;
  }
  .info-col--hours {
    left: 56px;
    display: flex;
    gap: 12px;
    font-size: 22px;
    line-height: 1.32;
  }
  .info-col--weeks {
    left: 306px;
    font-size: 28px;
    line-height: 1.2;
  }
  .info-col--cost {
    left: 584px;
    font-size: 21px;
    line-height: 1.35;
  }
  .col-rule {
    position: absolute;
    top: 936px;
    width: 0;
    height: 118px;
    border-left: 2px solid var(--white);
  }
  .col-rule--a { left: 284px; }
  .col-rule--b { left: 540px; }
  .script-label {
    font-family: "Kaushan Script", cursive;
    text-transform: none;
    font-size: 24px;
    font-weight: 400;
    display: block;
    line-height: 1.3;
  }
  .info-col--cost .script-label { margin-left: 28px; }
  .week { display: block; }
  .week::before { content: "\25B8\00a0"; font-size: 20px; vertical-align: 3px; }
  .cost { display: flex; align-items: center; gap: 10px; margin-top: 4px; }
  .divider {
    position: absolute;
    left: 36px;
    top: 1076px;
    width: 746px;
    border-top: 2px dashed var(--white);
  }
  .register {
    position: absolute;
    left: 62px;
    top: 1104px;
    font-family: "Kaushan Script", cursive;
    font-size: 36px;
    transform: rotate(-6deg);
    transform-origin: left center;
  }
  .footer-block {
    position: absolute;
    top: 1094px;
    display: flex;
    gap: 8px;
    text-transform: uppercase;
    font-size: 15px;
    font-weight: 500;
    line-height: 1.35;
  }
  .footer-block--location { left: 326px; }
  .footer-block--contact { left: 548px; }
  .footer-block .script-label { font-size: 20px; color: var(--navy); }
</style>
</head>
<body>
<main class="flyer">
  <svg class="flyer__backdrop" width="818" height="1200" viewBox="0 0 818 1200">
    <defs>
      <linearGradient id="fieldTone" x1="0" y1="0" x2="1" y2="1">
        <stop offset="0" stop-color="#8c9a5a"/>
        <stop offset="0.6" stop-color="#4f5a2e"/>
        <stop offset="1" stop-color="#6a5a3a"/>
      </linearGradient>
    </defs>
    <rect width="818" height="1200" fill="#ffffff"/>
    <rect class="hero-photo" x="0" y="0" width="818" height="560" fill="url(#fieldTone)" role="img" aria-label="Photo of a young player in a red batting helmet on a grass field"/>
    <path d="M0,430 C250,320 520,390 818,290 L818,335 C520,430 250,370 0,480 Z" fill="#ec1f27"/>
    <path d="M0,480 C250,370 520,430 818,335 L818,820 L0,820 Z" fill="#ffffff"/>
    <path d="M0,770 C200,800 500,790 818,740 L818,772 C520,830 250,860 0,872 Z" fill="#1f3a6e"/>
    <path d="M0,890 C250,875 520,840 818,790 L818,1200 L0,1200 Z" fill="#ec1f27"/>
    <circle cx="192" cy="374" r="96" fill="#ffffff" stroke="#ec1f27" stroke-width="8"/>
  </svg>

  <div class="brand-badge">Kestrel</div>

  <svg class="flyer__titles" width="818" height="1200" viewBox="0 0 818 1200" aria-hidden="false">
    <text class="title-main" x="69" y="643" textLength="616" lengthAdjust="spacingAndGlyphs" font-family="Oswald, sans-serif" font-weight="600" font-size="132"><tspan fill="#ec1f27">SUMMER</tspan><tspan fill="#1f3a6e">CAMP</tspan></text>
    <text class="title-year" transform="translate(718,641) rotate(-90)" x="0" y="0" textLength="100" lengthAdjust="spacingAndGlyphs" font-family="Oswald, sans-serif" font-weight="600" font-size="34" fill="#ec1f27">2017</text>
    <text class="host-note" font-family="Oswald, sans-serif" font-weight="700" font-size="11.5" fill="#1b1b1b">
      <tspan x="69" y="684" textLength="400" lengthAdjust="spacingAndGlyphs">HOSTED BY "KESTREL BASEBALL" AFFILIATED WITH THE HARBOR COMETS TRAVEL</tspan>
      <tspan x="69" y="711" textLength="360" lengthAdjust="spacingAndGlyphs">BASEBALL &amp; SOFTBALL CLUB AND THE MAPLE RIDGE YOUTH LEAGUE</tspan>
    </text>
  </svg>

  <div class="title-script">Softball</div>
  <div class="title-sub">for boys and girls</div>
  <div class="affiliate-badge" aria-label="Affiliate league badge"></div>

  <div class="players">
    <svg width="30" height="38" viewBox="0 0 34 40" aria-hidden="true">
      <circle cx="9" cy="6" r="5" fill="#1f3a6e"/><rect x="3" y="13" width="12" height="25" rx="3" fill="#1f3a6e"/>
      <circle cx="25" cy="6" r="5" fill="#1f3a6e"/><rect x="19" y="13" width="12" height="25" rx="3" fill="#1f3a6e"/>
    </svg>
    <div class="players__label">Players<br>Ages</div>
  </div>
  <div class="players__ages">5 - 11</div>

  <div class="info-col info-col--hours">
    <svg width="28" height="32" viewBox="0 0 30 34" aria-hidden="true">
      <circle cx="15" cy="19" r="12" fill="none" stroke="#ffffff" stroke-width="3"/>
      <rect x="11" y="1" width="8" height="4" fill="#ffffff"/>
      <path d="M15 19 V12 M15 19 L20 22" stroke="#ffffff" stroke-width="3" fill="none"/>
    </svg>
    <div>Full Day<br>9:30am - 2:30pm<br>Half Day<br>9:30am - 11:30am</div>
  </div>
  <div class="col-rule col-rule--a"></div>
  <div class="info-col info-col--weeks">
    <span class="script-label">Weeks of</span>
    <span class="week">July 10th - 14th</span>
    <span class="week">July 17th - 21st.</span>
  </div>
  <div class="col-rule col-rule--b"></div>
  <div class="info-col info-col--cost">
    <span class="script-label">Cost:</span>
    <div class="cost">
      <svg width="30" height="30" viewBox="0 0 34 34" aria-hidden="true">
        <circle cx="17" cy="17" r="16" fill="#ffffff"/>
        <text x="17" y="25" text-anchor="middle" font-family="Oswald, sans-serif" font-weight="700" font-size="22" fill="#ec1f27">$</text>
      </svg>
      <div>$295 / Full Day<br>$195/ Half Day</div>
    </div>
  </div>

  <div class="divider"></div>

  <div class="register">Register today!</div>

  <div class="footer-block footer-block--location">
    <svg width="16" height="24" viewBox="0 0 18 26" aria-hidden="true">
      <path d="M9 0 C4 0 0 4 0 9 C0 16 9 26 9 26 C9 26 18 16 18 9 C18 4 14 0 9 0 Z" fill="#1f3a6e"/>
      <circle cx="9" cy="9" r="3.5" fill="#ec1f27"/>
    </svg>
    <div><span class="script-label">Camp Location:</span>MRYL, Route 9C<br>Birch Hollow.</div>
  </div>

  <div class="footer-block footer-block--contact">
    <svg width="14" height="24" viewBox="0 0 16 26" aria-hidden="true">
      <rect x="0" y="0" width="16" height="26" rx="3" fill="#1f3a6e"/>
      <rect x="3" y="4" width="10" height="14" fill="#ec1f27"/>
      <circle cx="8" cy="22" r="1.6" fill="#ffffff"/>
    </svg>
    <div><span class="script-label">Contact:</span>Phone 555-240-7813<br>Email info@kestrelball.example</div>
  </div>
</main>
</body>
</html>
```